Business Card Design - Photographer

I am a landscape photographer and I require a business card design. 

I require two designs:
1)  a double sided business card
 and
b)  a single sided business card 

The single sided design can either be the same as the double sided (with just one side having all the information)....or it can be an entire new design. Its up to you.

My corporate colours are (CMYK):

Blue   69, 32, 0, 0
Grey  72,  64,  47,  31
Green  32,  2,  91,  0
Yellow   0, 19, 92, 0
Orange  0, 39, 75, 0

Colour space in final file should be in CMYK.

The details that need to be included on the card:

- Use the provided Logo
- Name: Wiktor Baranowski
- Email:   sales@vistalumeworks.com.au
- Website:    vistalumeworks.com.au
- Twitter:    twitter.com/vistalumeworks
- Facebook:   facebook.com/vistalumeworks
- Mobile  0417 539 662

Please use the attached template to design the logo to the specified size, including the marked bleed lines. I have also attached my logo in PNG (transparent background) and ai format for you to use.

The final file should be:
- Photoshop version with layers so I can edit the name/text etc. All non vector files should be high resolution at 1039 x 697 pixels at 300 dpi.

I also require a file as:
- Vector based PDF

Anyway questions please contact me.

Thank you

Industry/Entity Type

Landscape

Logo styles of interest
Pictorial/Combination Logo
Abstract Logo
Wordmark Logo
Lettermark Logo
Requirements
Must have
• The details that need to be included on the card:

- Use the provided Logo
- Name: Wiktor Baranowski
- Email: sales@vistalumeworks.com.au
- Website: vistalumeworks.com.au
- Twitter: twitter.com/vistalumeworks
- Facebook: facebook.com/vistalumeworks
- Mobile 0417 539 662

```html
<!DOCTYPE html>
<html lang="en">
<head>
<meta charset="utf-8">
<title>Vistalume Works – Business Card</title>
<link rel="stylesheet" href="https://fonts.googleapis.com/css2?family=Cinzel:wght@400;600;700&display=swap">
<style>
  :root {
    --backdrop: #8e9194;
    --card: #ffffff;
    --ink: #3f4152;
    --accent-blue: #3b9bd8;
    --band: #3f4152;
    --band-text: #ffffff;
  }
  * { box-sizing: border-box; margin: 0; padding: 0; }
  html, body {
    width: 1200px;
    height: 765px;
    overflow: hidden;
    background: var(--backdrop);
  }
  .canvas {
    position: relative;
    width: 1200px;
    height: 765px;
  }
  .business-card {
    position: absolute;
    left: 90px;
    top: 102px;
    width: 1022px;
    height: 581px;
    background: var(--card);
    border-radius: 32px;
    overflow: hidden;
    font-family: "Cinzel", "Trajan Pro", serif;
    color: var(--ink);
  }
  .brand-mark {
    position: absolute;
    left: 50%;
    top: 26px;
    width: 205px;
    height: 205px;
    margin-left: -95px;
  }
  .centered-line {
    position: absolute;
    left: 0;
    right: 0;
    text-align: center;
    white-space: nowrap;
  }
  .brand-name {
    top: 250px;
    height: 56px;
    line-height: 56px;
    font-size: 54px;
    font-weight: 400;
    letter-spacing: 1px;
  }
  .brand-rule {
    position: absolute;
    left: 50%;
    top: 305px;
    width: 526px;
    height: 2px;
    margin-left: -263px;
    background: var(--ink);
  }
  .tagline {
    top: 318px;
    height: 24px;
    line-height: 24px;
    font-size: 20px;
    font-weight: 600;
    letter-spacing: 4px;
  }
  .holder-name {
    top: 372px;
    height: 38px;
    line-height: 38px;
    font-size: 32px;
    font-weight: 600;
    letter-spacing: 1px;
  }
  .contact-line {
    height: 28px;
    line-height: 28px;
    font-size: 21px;
    letter-spacing: 0.5px;
    text-transform: lowercase;
  }
  .contact-line.primary { top: 424px; }
  .contact-line.social { top: 459px; }
  .contact-label {
    color: var(--accent-blue);
    font-weight: 700;
    text-transform: uppercase;
    font-size: 23px;
  }
  .contact-gap { display: inline-block; width: 6px; }
  .divider-rule {
    position: absolute;
    left: 0;
    right: 0;
    top: 496px;
    height: 4px;
    background: var(--band);
  }
  .footer-band {
    position: absolute;
    left: 0;
    right: 0;
    top: 508px;
    bottom: 0;
    background: var(--band);
    display: flex;
    align-items: center;
    justify-content: center;
  }
  .website {
    color: var(--band-text);
    font-size: 30px;
    font-weight: 600;
    letter-spacing: 0.5px;
    white-space: nowrap;
  }
  .website-small {
    font-size: 22px;
    text-transform: lowercase;
  }
</style>
</head>
<body>
  <main class="canvas">
    <section class="business-card">
      <svg class="brand-mark" viewBox="0 0 205 205" role="img" aria-label="Brand emblem area: half-circle wave and colourful leaf tree illustration">
        <circle cx="102.5" cy="102.5" r="100" fill="var(--ink)"/>
      </svg>

      <h1 class="centered-line brand-name">VISTALUME WORKS</h1>
      <div class="brand-rule"></div>
      <p class="centered-line tagline">FINE ART PHOTOGRAPHY</p>

      <h2 class="centered-line holder-name">Wiktor Baranowski</h2>

      <p class="centered-line contact-line primary">
        <span class="contact-label">M</span> : 0417 539 662<span class="contact-gap"></span>
        <span class="contact-label">E</span> : sales@vistalumeworks.com.au
      </p>
      <p class="centered-line contact-line social">
        <span class="contact-label">F</span> : fanboard.com/vistalumeworks<span class="contact-gap"></span>
        <span class="contact-label">T</span> : talkstream.com/vistalumeworks
      </p>

      <div class="divider-rule"></div>
      <footer class="footer-band">
        <span class="website"><span class="website-small">www.</span>VISTALUMEWORKS<span class="website-small">.com.au</span></span>
      </footer>
    </section>
  </main>
</body>
</html>
```